Create modern and sleek business card for luxury real estate company

We're a "boutique" real estate office looking for a design that gets across a highly modern luxury brand. Blacks and whites are probably the best colors unless we try a silver foil for the logo. I've attached a version of our current logo here. I'd like to swap out the current font on there with Gotham Light Regular.

I'm looking to have one side of the card have the logo with the space for our agents info on the other side.

Target Market(s)

Young professionals in a "luxury" headspace

Industry/Entity Type

Real estate

Contact Information for Business Card

A place for agent name, cell number, website. The slogan "Simply Rethinking Real Estate".

Font styles to use
Other font styles liked:
• Gotham Regular

Colors

Designer to choose only greyscale colors for use in the design.

Requirements
Must have
• Matte black as the background color. Clean lines and use of contrast. A specific design aspect that will use silver foil.
Nice to have
• Up in the air on integrating a QR code
Should not have
• Any houses or other real estate related design (ex: a clip art house)

```html
<!DOCTYPE html>
<html lang="en">
<head>
<meta charset="utf-8">
<title>Halden Realty — Business Card</title>
<link href="https://fonts.googleapis.com/css2?family=Open+Sans:wght@400;700&display=swap" rel="stylesheet">
<style>
  :root {
    --scene-bg: #3a3a3a;
    --card-black: #0b0b0b;
    --ink-white: #f4f4f4;
    --ink-grey: #7d7d7d;
    --rule-grey: #5a5a5a;
    --silver: #d9d9d9;
    --pattern-dark: #151515;
    --pattern-light: #2a2a2a;
  }
  * { margin: 0; padding: 0; box-sizing: border-box; }
  html, body {
    width: 1200px; height: 801px; overflow: hidden;
    background: var(--scene-bg);
    font-family: "Open Sans", Arial, sans-serif;
  }
  .canvas {
    position: relative; width: 1200px; height: 801px;
    display: flex; align-items: center; justify-content: center; gap: 60px;
  }
  .card {
    position: relative; width: 520px; height: 297px;
    background: var(--card-black);
    overflow: hidden;
  }
  /* Agent side */
  .card--agent {
    display: flex; align-items: center; justify-content: center; gap: 28px;
  }
  .agent-id { text-align: right; }
  .agent-name {
    color: var(--ink-white); font-weight: 700; font-size: 22px;
    letter-spacing: 1px; text-transform: uppercase;
  }
  .agent-title { color: var(--ink-grey); font-size: 15px; margin-top: 2px; }
  .divider { width: 1px; height: 78px; background: var(--rule-grey); }
  .contact-list { list-style: none; }
  .contact-item {
    display: flex; align-items: center; gap: 8px;
    color: var(--ink-white); font-size: 15px; line-height: 24px;
  }
  .contact-item svg { width: 11px; height: 11px; fill: var(--ink-grey); flex: none; }
  /* Brand side */
  .brand-pattern {
    position: absolute; inset: 0;
    background: linear-gradient(135deg, var(--pattern-dark) 0%, var(--pattern-light) 100%);
  }
  .brand-mark {
    position: absolute; right: 38px; bottom: 60px;
    display: flex; align-items: center; gap: 12px;
  }
  .brand-circle {
    width: 50px; height: 50px; border-radius: 50%;
    border: 2px solid var(--silver);
  }
  .brand-name {
    color: var(--silver); font-size: 22px; font-weight: 400;
    letter-spacing: 2px; line-height: 26px; text-transform: uppercase;
  }
</style>
</head>
<body>
<main class="canvas">
  <section class="card card--agent" aria-label="Agent side">
    <div class="agent-id">
      <p class="agent-name">Adrian Vallmer</p>
      <p class="agent-title">President</p>
    </div>
    <div class="divider"></div>
    <ul class="contact-list">
      <li class="contact-item">
        <svg viewBox="0 0 12 12" aria-hidden="true"><path d="M2.5 1l2 2.2-1 1.3a7 7 0 0 0 4 4l1.3-1 2.2 2-1.2 1.5C5.5 11 1 6.5 1 2.2z"/></svg>
        555-318-7420
      </li>
      <li class="contact-item">
        <svg viewBox="0 0 12 12" aria-hidden="true"><path d="M1 3h10v6H1z M1 3l5 3.5L11 3" stroke="#0b0b0b" stroke-width="0.8"/></svg>
        info@haldenrealty.com
      </li>
      <li class="contact-item">
        <svg viewBox="0 0 12 12" aria-hidden="true"><circle cx="6" cy="6" r="5"/></svg>
        www.haldenrealty.com
      </li>
    </ul>
  </section>

  <section class="card card--brand" aria-label="Brand side">
    <div class="brand-pattern" role="img" aria-label="Repeating tone-on-tone emblem pattern across the card"></div>
    <div class="brand-mark">
      <span class="brand-circle"></span>
      <p class="brand-name">Halden<br>Realty</p>
    </div>
  </section>
</main>
</body>
</html>
```